Calder Vossik - Cinematographer

NEED:
I'm looking for a sleek, professional, modern business card that will give give the recipient the impression that they can trust their production will go smoothly by hiring me. I will bring creativity and knowledge to their shoot, so that we can create powerful images.
I am looking for a card with a strong style and design ethos that could be expanded to a website and a full visual/graphic/design entity for me.
ABOUT ME:
I am a mid-twenties cinematographer, I work on music video, narrative short, commercial, and corporate projects. I blend the science and artistry of cameras and filmmaking to tell a story. I'm an artist, a technician, and a manager.
DESIGN:
I like sleek, simple design. Black, dark grays, white, dark navy, steel blues, I love cyan, but also cyan and red. I am not a fan of earthy tones. I generally prefer modern, san-serif fonts over serifs. My old logo was based on an aperture, a multi-blade device at the back of a lens that controls how much light passes through, but I made it with so many colors, that it doesn't necessarily lend itself to a specific color-scheme or design ethos. I liked that the aperture design provided a sense of the technical requirements of my job. I'm a fan of matte business cards, but am open to plenty of specialty print processes to make an outstanding card.
ATTACHED FILES:
My Old Rainbox Aperture Logo, plus a few designs I've tried playing around with, but am not tied to. I AM OPEN TO NEW DESIGNS, DO NOT FEEL TIED TO THIS.
**I've pulled my old logo down from the attached files, and instead attached other business cards I like, so as not to mislead you where I would like to go.
INFO:
Name: Calder Vossik
Job: Cinematographer
Email: ccvossik@lumenpost.net
Phone: 415.555.0193
Website: caldervossik.com
Updates
I'm adding some images of other cards that I like, and removing my old logo, since I'm looking for something new, and don't want that old logo to push anyone a certain direction.

```html
<!DOCTYPE html>
<html lang="en">
<head>
<meta charset="utf-8">
<title>Calder Vossik — Cinematographer Business Card</title>
<link rel="stylesheet" href="https://fonts.googleapis.com/css2?family=Archivo:wght@400;800&family=Arimo:wght@400&display=swap">
<style>
  :root {
    --ink: #111111;
    --paper: #ffffff;
    --muted: #555555;
    --backdrop: #d9d9d9;
    --card-shadow: rgba(0, 0, 0, 0.18);
  }
  * { box-sizing: border-box; margin: 0; padding: 0; }
  html, body {
    width: 1200px;
    height: 926px;
    overflow: hidden;
    background: var(--backdrop);
  }
  .sheet {
    width: 1200px;
    height: 926px;
    display: flex;
    align-items: center;
    justify-content: center;
    gap: 60px;
  }
  .card {
    width: 525px;
    height: 300px;
    position: relative;
    box-shadow: 0 6px 18px var(--card-shadow);
  }
  /* Front */
  .card--front { background: var(--paper); color: var(--ink); }
  .brand-mark {
    position: absolute;
    left: 22px;
    top: 24px;
    width: 120px;
    height: 120px;
    border-radius: 50%;
    background: var(--ink);
  }
  .divider {
    position: absolute;
    left: 170px;
    top: 22px;
    width: 2px;
    height: 126px;
    background: var(--ink);
  }
  .identity {
    position: absolute;
    left: 190px;
    top: 62px;
    right: 24px;
  }
  .identity__name {
    font-family: "Archivo", "Arial Black", sans-serif;
    font-weight: 800;
    font-size: 35px;
    line-height: 1;
    letter-spacing: 0.5px;
    text-transform: uppercase;
    white-space: nowrap;
  }
  .identity__role {
    font-family: "Arimo", Arial, sans-serif;
    font-size: 21px;
    color: var(--muted);
    letter-spacing: 1px;
    margin-top: 4px;
    text-align: right;
    padding-right: 6px;
  }
  .contacts {
    position: absolute;
    left: 150px;
    top: 192px;
    list-style: none;
    font-family: "Arimo", Arial, sans-serif;
    font-size: 15px;
    line-height: 22px;
    color: var(--ink);
  }
  .contacts__item { display: flex; align-items: center; gap: 14px; }
  .contacts__icon { width: 12px; height: 12px; flex: none; color: var(--muted); }
  /* Back */
  .card--back {
    background: var(--ink);
    color: var(--paper);
    display: flex;
    flex-direction: column;
    align-items: center;
    justify-content: center;
  }
  .back-mark {
    width: 96px;
    height: 96px;
    border-radius: 50%;
    background: var(--paper);
  }
  .back-wordmark {
    font-family: "Archivo", "Arial Black", sans-serif;
    font-weight: 800;
    font-size: 20px;
    letter-spacing: 2px;
    text-transform: uppercase;
    margin-top: 16px;
  }
  .back-url {
    font-family: "Arimo", Arial, sans-serif;
    font-size: 13px;
    letter-spacing: 4px;
    margin-top: 14px;
  }
</style>
</head>
<body>
<main class="sheet">
  <section class="card card--front" aria-label="Business card front">
    <div class="brand-mark" aria-hidden="true"></div>
    <div class="divider" aria-hidden="true"></div>
    <div class="identity">
      <h1 class="identity__name">Calder Vossik</h1>
      <p class="identity__role">cinematographer</p>
    </div>
    <ul class="contacts">
      <li class="contacts__item">
        <svg class="contacts__icon" viewBox="0 0 12 12" aria-hidden="true"><rect x="0.5" y="2" width="11" height="8" fill="none" stroke="currentColor"/><path d="M0.5 2 L6 6.5 L11.5 2" fill="none" stroke="currentColor"/></svg>
        <span>ccvossik@lumenpost.net</span>
      </li>
      <li class="contacts__item">
        <svg class="contacts__icon" viewBox="0 0 12 12" aria-hidden="true"><rect x="3" y="0.5" width="6" height="11" rx="1" fill="none" stroke="currentColor"/><line x1="5" y1="9.5" x2="7" y2="9.5" stroke="currentColor"/></svg>
        <span>415.555.0193</span>
      </li>
      <li class="contacts__item">
        <svg class="contacts__icon" viewBox="0 0 12 12" aria-hidden="true"><circle cx="6" cy="6" r="5.5" fill="none" stroke="currentColor"/><ellipse cx="6" cy="6" rx="2.4" ry="5.5" fill="none" stroke="currentColor"/><line x1="0.5" y1="6" x2="11.5" y2="6" stroke="currentColor"/></svg>
        <span>www.caldervossik.com</span>
      </li>
    </ul>
  </section>

  <section class="card card--back" aria-label="Business card back">
    <div class="back-mark" aria-hidden="true"></div>
    <p class="back-wordmark">Calder Vossik</p>
    <p class="back-url">www.caldervossik.com</p>
  </section>
</main>
</body>
</html>
```